Bright Harbor Painters Banner

Create a banner that displays and reinforces Bright Harbor Painters’ brand identity while promoting our interior painting services. The banner will be displayed at indoor venues through the winter. The design should be clean, professional, and visually recognizable to both new and returning customers. See attached design brief & logo source files.

```html
<!DOCTYPE html>
<html lang="en">
<head>
<meta charset="utf-8">
<title>Bright Harbor Painters Banner</title>
<link rel="stylesheet" href="https://fonts.googleapis.com/css2?family=Montserrat:wght@600;700;800&display=swap">
<style>
  :root {
    --backdrop: #3e413d;
    --green-deep: #6a8554;
    --green-light: #8ca276;
    --green-brand: #6c9243;
    --ink: #2e302d;
    --white: #ffffff;
    --paper: #f4f5f4;
    --pill: #464845;
  }
  * { margin: 0; padding: 0; box-sizing: border-box; }
  html, body {
    width: 1068px; height: 1200px; overflow: hidden;
    background: var(--backdrop);
    font-family: "Montserrat", sans-serif;
  }
  .banner {
    position: absolute; left: 34px; top: 400px;
    width: 1000px; height: 400px;
    background: var(--paper);
    overflow: hidden;
    box-shadow: 0 10px 30px rgba(0,0,0,.35);
  }
  .paint-field { position: absolute; inset: 0; }
  .roller-art { position: absolute; left: 0; top: 0; width: 300px; height: 400px; }
  .headline {
    position: absolute; left: 48px; top: 14px;
    font-size: 101px; font-weight: 800; line-height: 1;
    color: var(--white); letter-spacing: 1px; white-space: nowrap;
  }
  .services-title {
    position: absolute; left: 329px; top: 120px;
    font-size: 27px; font-weight: 800; letter-spacing: 4.8px;
    color: var(--ink); white-space: nowrap;
  }
  .service {
    position: absolute; display: flex; align-items: flex-start; gap: 14px;
    font-size: 29px; font-weight: 700; line-height: 1.1; color: var(--white);
    white-space: nowrap;
  }
  .service svg { width: 24px; height: 24px; flex: none; margin-top: 5px; }
  .brand-name {
    position: absolute; left: 206px; top: 272px; width: 226px;
    display: flex; flex-direction: column; align-items: center; gap: 8px;
    color: var(--green-brand); font-weight: 800;
    font-size: 22px; line-height: 1.1; text-transform: uppercase;
    text-align: center; white-space: nowrap;
  }
  .brand-dot { width: 40px; height: 40px; border-radius: 50%; background: var(--green-brand); flex: none; }
  .cta-pill {
    position: absolute; left: 447px; top: 285px; width: 498px; height: 37px;
    border-radius: 19px; background: var(--pill);
    color: var(--white); font-size: 25px; font-weight: 700;
    display: flex; align-items: center; justify-content: center;
    white-space: nowrap;
  }
  .cta-url {
    position: absolute; left: 447px; top: 322px; width: 498px;
    text-align: center; font-size: 45px; font-weight: 700;
    color: var(--ink); letter-spacing: -0.5px; white-space: nowrap;
  }
  .cta-url .accent { color: var(--green-brand); }
</style>
</head>
<body>
  <div class="banner">
    <svg class="paint-field" viewBox="0 0 1000 400" preserveAspectRatio="none" aria-hidden="true">
      <defs>
        <linearGradient id="fieldGrad" x1="0" y1="0" x2="1" y2="0">
          <stop offset="0" stop-color="#6a8554"/>
          <stop offset="1" stop-color="#8ca276"/>
        </linearGradient>
      </defs>
      <path d="M0 0 H1000 V226 C960 240 930 232 900 246 C850 262 800 250 740 258 C680 262 620 248 560 256 C500 262 440 250 380 254 C320 256 260 244 200 250 C140 254 80 246 0 256 Z" fill="url(#fieldGrad)"/>
    </svg>

    <svg class="roller-art" viewBox="0 0 300 400" role="img" aria-label="Paint roller with a green-coated roller cover">
      <defs>
        <linearGradient id="rollerGrad" x1="0" y1="0" x2="0" y2="1">
          <stop offset="0" stop-color="#8fa57a"/>
          <stop offset="1" stop-color="#66804f"/>
        </linearGradient>
      </defs>
      <rect x="60" y="123" width="229" height="85" rx="12" fill="url(#rollerGrad)"/>
      <rect x="28" y="160" width="134" height="240" rx="6" fill="#b9bcb8" opacity=".4"/>
    </svg>

    <div class="headline">PAINT SMARTER</div>
    <div class="services-title">INTERIOR PAINTING SERVICES</div>

    <div class="service" style="left:329px; top:154px;">
      <svg viewBox="0 0 24 24"><circle cx="12" cy="12" r="10.5" fill="#ffffff" stroke="#2e302d" stroke-width="2"/><path d="M7 12.3l3.3 3.2L17 8.8" fill="none" stroke="#2e302d" stroke-width="2.4" stroke-linecap="round" stroke-linejoin="round"/></svg>Walls</div>
    <div class="service" style="left:329px; top:196px;">
      <svg viewBox="0 0 24 24"><circle cx="12" cy="12" r="10.5" fill="#ffffff" stroke="#2e302d" stroke-width="2"/><path d="M7 12.3l3.3 3.2L17 8.8" fill="none" stroke="#2e302d" stroke-width="2.4" stroke-linecap="round" stroke-linejoin="round"/></svg>Ceilings</div>
    <div class="service" style="left:543px; top:154px;">
      <svg viewBox="0 0 24 24"><circle cx="12" cy="12" r="10.5" fill="#ffffff" stroke="#2e302d" stroke-width="2"/><path d="M7 12.3l3.3 3.2L17 8.8" fill="none" stroke="#2e302d" stroke-width="2.4" stroke-linecap="round" stroke-linejoin="round"/></svg>Trim</div>
    <div class="service" style="left:543px; top:196px;">
      <svg viewBox="0 0 24 24"><circle cx="12" cy="12" r="10.5" fill="#ffffff" stroke="#2e302d" stroke-width="2"/><path d="M7 12.3l3.3 3.2L17 8.8" fill="none" stroke="#2e302d" stroke-width="2.4" stroke-linecap="round" stroke-linejoin="round"/></svg>Cabinets</div>
    <div class="service" style="left:765px; top:154px;">
      <svg viewBox="0 0 24 24"><circle cx="12" cy="12" r="10.5" fill="#ffffff" stroke="#2e302d" stroke-width="2"/><path d="M7 12.3l3.3 3.2L17 8.8" fill="none" stroke="#2e302d" stroke-width="2.4" stroke-linecap="round" stroke-linejoin="round"/></svg>Drywall<br>Repair</div>

    <div class="brand-name"><span class="brand-dot"></span><span>Bright Harbor<br>Painters</span></div>

    <div class="cta-pill">Book a Free Estimate at</div>
    <div class="cta-url">www.<span class="accent">bhpainters</span>.com</div>
  </div>
</body>
</html>
```